New Business Card Design for Manufacturing

We are an engineering/manufacturing company that offers Advanced machining/assembly/engineering services, as well as innovative products for the heavy duty engine cooling markets.

We are looking to get a new business card designed that is clean and modern looking, but still fits the wide range of technical/skilled work we do.

- We hope to use this design as the base for other design work in new Presentations, web, and print work.

Industry/Entity Type

Engineering

Contact Information for Business Card

Our preferred color of blue is (RGB) 22/71/159 but can vary slightly from that color. Our content will be our Logo and full company name (Vantrell Forge Works, Inc.), company address, name, job title, phone number with extension, cell number, fax number, website, and email address on the cards.
We'd like the full company name next to the logo, but we are open to other interpretations of that layout.
Preferably, we would like the back side to be clean with just our logo, and the front to contain all of the contact information.

Colors
2f74b4
0355a3
85abd2

Requirements
Must have
• - Logo, company name, needed content - We are open to interpretation beyond that.
• - Standard size business card.
• - Horizontal orientation.
• - Enough space for lengthy names / job titles (for example, a job title could read "Directory of Human Resources" or "V.P. of Governmental Affairs"). We need this to look clean, whether the title be short (CEO) or long (as described above).

```html
<!DOCTYPE html>
<html lang="en">
<head>
<meta charset="utf-8">
<title>Vantrell Forge Works — Business Card</title>
<link rel="stylesheet" href="https://fonts.googleapis.com/css2?family=Archivo:wght@400;600;800&family=Lato:wght@400;700&display=swap">
<style>
  :root {
    --brand-blue: #16479f;
    --mid-blue: #0355a3;
    --bright-blue: #1f6cc4;
    --soft-blue: #85abd2;
    --pale-blue: #b3cbe6;
    --paper: #f6f7f9;
    --stage: #e4e7ec;
    --white: #ffffff;
  }
  * { box-sizing: border-box; margin: 0; padding: 0; }
  html, body { width: 1200px; height: 780px; overflow: hidden; }
  body {
    background: var(--stage);
    font-family: "Lato", sans-serif;
    display: flex;
    align-items: center;
    justify-content: center;
    gap: 40px;
  }
  .card {
    position: relative;
    width: 525px;
    height: 300px;
    overflow: hidden;
    box-shadow: 0 6px 18px rgba(20, 40, 80, 0.18);
  }

  /* Front */
  .card--front { background: var(--paper); }
  .front__panel-name {
    position: absolute;
    top: 0; right: 0;
    width: 210px; height: 150px;
    background: linear-gradient(160deg, var(--pale-blue), var(--soft-blue));
    clip-path: polygon(22% 0, 100% 0, 100% 100%, 0 100%);
  }
  .front__band-contact {
    position: absolute;
    left: 0; right: 0;
    top: 150px; height: 116px;
    background: linear-gradient(90deg, var(--bright-blue), var(--mid-blue));
  }
  .front__brand {
    position: absolute;
    top: 40px; left: 30px;
    display: flex;
    align-items: center;
    gap: 12px;
  }
  .brand__square {
    width: 44px; height: 44px;
    background: var(--brand-blue);
  }
  .brand__name {
    font-family: "Archivo", sans-serif;
    font-weight: 800;
    color: var(--brand-blue);
    font-size: 19px;
    line-height: 1.02;
    text-transform: uppercase;
  }
  .front__person {
    position: absolute;
    top: 58px; right: 22px;
    width: 140px;
    text-align: left;
    color: var(--brand-blue);
  }
  .person__name {
    font-family: "Archivo", sans-serif;
    font-weight: 600;
    font-size: 16px;
    text-transform: uppercase;
    letter-spacing: 0.3px;
  }
  .person__title { font-size: 12px; color: #2f5f97; margin-top: 2px; }
  .front__contacts {
    position: absolute;
    top: 164px; left: 30px;
    list-style: none;
    color: var(--white);
    font-size: 12.5px;
  }
  .contact__item {
    display: flex;
    align-items: center;
    gap: 8px;
    height: 22px;
  }
  .contact__icon { width: 15px; height: 15px; flex: none; }
  .front__address {
    position: absolute;
    left: 0; right: 0; bottom: 0;
    height: 34px;
    display: flex;
    align-items: center;
    padding-left: 30px;
    color: var(--mid-blue);
    font-size: 12.5px;
  }

  /* Back */
  .card--back {
    background: radial-gradient(ellipse at 60% 45%, var(--bright-blue), var(--mid-blue) 75%);
  }
  .back__strip {
    position: absolute;
    left: 0; right: 0; bottom: 0;
    height: 40px;
    background: linear-gradient(90deg, #8fb0d4, #6f97c6);
    display: flex;
    align-items: center;
    justify-content: center;
    color: rgba(255, 255, 255, 0.85);
    font-size: 12px;
    letter-spacing: 4px;
  }
  .back__brand {
    position: absolute;
    top: 92px; left: 0; right: 0;
    display: flex;
    justify-content: center;
    align-items: center;
    gap: 16px;
  }
  .back__brand .brand__square { width: 58px; height: 58px; background: var(--white); }
  .back__brand .brand__name { color: var(--white); font-size: 24px; }
</style>
</head>
<body>

<section class="card card--front" aria-label="Business card front">
  <div class="front__panel-name"></div>
  <div class="front__band-contact"></div>

  <div class="front__brand">
    <span class="brand__square"></span>
    <p class="brand__name">Vantrell<br>Forge<br>Works, Inc.</p>
  </div>

  <div class="front__person">
    <p class="person__name">Dorian Pell</p>
    <p class="person__title">Founder</p>
  </div>

  <ul class="front__contacts">
    <li class="contact__item">
      <svg class="contact__icon" viewBox="0 0 16 16"><circle cx="8" cy="8" r="7.3" fill="none" stroke="#fff" stroke-width="1.2"/><path d="M5.5 4.5h2l.6 2-1.1.8a5 5 0 0 0 2.2 2.2l.8-1.1 2 .6v2c-3.8.3-6.8-2.7-6.5-6.5z" fill="#fff"/></svg>
      (555) 204-3318
    </li>
    <li class="contact__item">
      <svg class="contact__icon" viewBox="0 0 16 16"><circle cx="8" cy="8" r="7.3" fill="none" stroke="#fff" stroke-width="1.2"/><rect x="5.8" y="3.8" width="4.4" height="8.4" rx="0.8" fill="#fff"/></svg>
      (555) 204-3390
    </li>
    <li class="contact__item">
      <svg class="contact__icon" viewBox="0 0 16 16"><circle cx="8" cy="8" r="7.3" fill="none" stroke="#fff" stroke-width="1.2"/><rect x="4.3" y="5.3" width="7.4" height="5.4" fill="#fff"/><path d="M4.3 5.3 8 8.3l3.7-3" fill="none" stroke="#1f6cc4" stroke-width="0.9"/></svg>
      hello@vantrellforge.com
    </li>
    <li class="contact__item">
      <svg class="contact__icon" viewBox="0 0 16 16"><circle cx="8" cy="8" r="7.3" fill="none" stroke="#fff" stroke-width="1.2"/><circle cx="8" cy="8" r="4" fill="none" stroke="#fff" stroke-width="1"/><path d="M4 8h8M8 4c-1.6 2.4-1.6 5.6 0 8M8 4c1.6 2.4 1.6 5.6 0 8" fill="none" stroke="#fff" stroke-width="0.8"/></svg>
      www.vantrellforge.com
    </li>
  </ul>

  <p class="front__address">PO Box 418, 27 Harlow Street, Geelong</p>
</section>

<section class="card card--back" aria-label="Business card back">
  <div class="back__brand">
    <span class="brand__square"></span>
    <p class="brand__name">Vantrell<br>Forge<br>Works, Inc.</p>
  </div>
  <p class="back__strip">www.vantrellforge.com</p>
</section>

</body>
</html>
```